Retail/Wholesale website graphic template

I need to design a new graphic template for a website for a client. The website will be a retail/wholesale company site with most pages dedicated to presentation. There will also be an online store and a blog. However, you don't need to worry about those. All I need from you is a graphic template for a generic site page.

It will need to include standard UI elements, in case I need those. I am attaching a more detailed assignment in .docx format.

The logo is also attached.

Target Market(s)

small business owners, (occasional) retail customers

Industry/Entity Type

Wholesale

Number of Pages Required

1 page

Font styles to use
Serif
Sans Serif

Colors
ec1f27
474747

Requirements
Must have
• must match logo, be clean, minimal and with slightly larger text size
Should not have
• must not be modern-looking where you have to scroll and scroll and scroll to get to the bottom of the homepage. most of my visitors are "old" people, they do not get this type of design.

```html
<!DOCTYPE html>
<html lang="en">
<head>
<meta charset="utf-8">
<title>Corvane Imports</title>
<link rel="stylesheet" href="https://fonts.googleapis.com/css2?family=Raleway:wght@500;600;700&family=Open+Sans:wght@400;600&family=Roboto+Condensed:wght@400;700&display=swap">
<style>
:root{
  --red:#ec1f27;
  --red-deep:#b5121a;
  --maroon:#3a0a0d;
  --ink:#111111;
  --text:#474747;
  --muted:#666666;
  --white:#ffffff;
  --footer:#151515;
  --footer-base:#0d0d0d;
  --footer-text:#d8d8d8;
}
*{margin:0;padding:0;box-sizing:border-box}
html,body{width:1200px;height:2913px;overflow:hidden;background:var(--white)}
body{font-family:"Open Sans",Arial,sans-serif;color:var(--text)}
.page{position:relative;width:1200px;height:2913px;overflow:hidden}
.abs{position:absolute}

/* header */
.topbar{left:476px;top:0;width:724px;height:48px}
.topbar-item{top:12px;color:var(--white);font-size:17px;display:flex;align-items:center;gap:8px;white-space:nowrap}
.topbar-sep{top:0;width:1px;height:48px;background:rgba(255,255,255,.45)}
.social-dot{border-radius:50%;background:var(--ink)}
.brand{left:93px;top:56px;font-family:"Raleway",sans-serif;font-weight:700;font-size:40px;color:var(--red);letter-spacing:2px;display:flex;align-items:center;gap:12px}
.brand-square{width:22px;height:22px;background:var(--red)}
.nav a{position:absolute;top:94px;font-size:18px;color:var(--ink);text-decoration:none;white-space:nowrap}
.nav a.active{color:var(--red)}

/* hero */
.hero{left:0;top:153px;width:1200px;height:531px;background:linear-gradient(180deg,#6d6a6a 0%,#c98a4a 30%,#5c5a5c 55%,#3b3c44 100%)}
.hero-title{left:0;width:1200px;top:350px;text-align:center;font-family:"Roboto Condensed",sans-serif;font-weight:700;font-size:78px;color:var(--white)}
.hero-sub{left:0;width:1200px;top:452px;text-align:center;font-family:"Roboto Condensed",sans-serif;font-size:33px;color:var(--white)}
.hero-dot{left:1160px;width:10px;height:10px;border-radius:50%;background:var(--white)}

/* about */
.about-title{left:0;width:1200px;top:792px;text-align:center;font-family:"Raleway",sans-serif;font-weight:600;font-size:42px;color:var(--ink)}
.about-title span{color:var(--red)}
.about-lead{left:0;width:1200px;top:851px;text-align:center;font-size:21px;color:var(--ink)}
.about-text{left:195px;width:810px;top:893px;text-align:center;font-size:14.5px;line-height:27px;color:var(--muted)}

/* services */
.services{left:0;top:1109px;width:1200px;height:515px;background:linear-gradient(90deg,var(--red-deep) 0%,var(--red) 60%,var(--red) 75%)}
.services-dark{left:903px;top:1109px;width:297px;height:515px;background:linear-gradient(90deg,#6b0b10,var(--maroon))}
.worker{left:670px;top:1132px;width:394px;height:492px;background:linear-gradient(180deg,#e7b92a 0%,#3a3a44 30%,#c6a173 60%,#c9d33a 100%)}
.services-title{left:87px;top:1210px;font-family:"Raleway",sans-serif;font-weight:600;font-size:38px;color:var(--white)}
.services-text{left:87px;top:1266px;width:600px;font-size:15.5px;line-height:29px;color:var(--white)}
.service-item{font-size:17px;color:var(--white);display:flex;align-items:center;gap:14px;white-space:nowrap}

/* blog */
.blog-title{left:0;width:1200px;top:1803px;text-align:center;font-family:"Raleway",sans-serif;font-weight:600;font-size:40px;color:var(--ink)}
.card{top:1903px;width:315px}
.card-img{width:315px;height:194px;border:3px solid #e6e6e6}
.card-date{position:absolute;left:6px;top:52px;width:44px;background:var(--red);color:var(--white);text-align:center;font-size:21px;line-height:22px;padding:4px 0 2px}
.card-date small{display:block;font-size:10px;line-height:12px}
.card-year{position:absolute;left:6px;top:102px;width:44px;background:#3a3a3a;color:var(--white);text-align:center;font-size:13px;line-height:36px}
.card-title{margin-top:17px;font-family:"Raleway",sans-serif;font-weight:500;font-size:20px;color:var(--ink)}
.card-body{margin-top:6px;font-size:14.5px;line-height:21px;color:var(--text);padding-left:4px}
.card-more{margin-top:10px;font-size:14px;color:var(--red)}

/* cta strip */
.cta{left:0;top:2377px;width:1200px;height:76px;background:var(--red)}
.cta-text{left:216px;top:2398px;font-size:25px;color:var(--white);font-family:"Raleway",sans-serif;font-weight:500}
.cta-phone{left:748px;top:2398px;font-size:25px;color:var(--white);display:flex;align-items:center;gap:10px}

/* footer */
.footer{left:0;top:2453px;width:1200px;height:460px;background:var(--footer)}
.footer-base{left:0;top:2806px;width:1200px;height:107px;background:var(--footer-base)}
.footer-brand{left:99px;top:2600px;width:214px;height:78px;display:flex;align-items:center;justify-content:center;font-family:"Raleway",sans-serif;font-weight:600;font-size:30px;color:var(--white);letter-spacing:3px}
.footer-head{top:2550px;font-size:21px;color:var(--white)}
.footer-link{font-size:15.5px;color:var(--footer-text)}
.contact-label{font-size:16px;font-weight:600;color:var(--white);display:flex;align-items:center;gap:10px}
.contact-value{font-size:14px;color:var(--footer-text)}
.foot-social{top:2788px;width:31px;height:31px;border-radius:50%;background:#2a2a2a;border:1px solid #3a3a3a}
.copyright{left:0;width:1200px;top:2862px;text-align:center;font-size:14.5px;color:#9a9a9a}
</style>
</head>
<body>
<div class="page">

  <!-- header -->
  <svg class="abs topbar" viewBox="0 0 724 48" width="724" height="48" aria-hidden="true"><polygon points="0,0 724,0 724,48 48,48" fill="#ec1f27"/></svg>
  <div class="abs topbar-item" style="left:544px">
    <svg width="16" height="16" viewBox="0 0 24 24"><path d="M6.6 10.8a15.5 15.5 0 0 0 6.6 6.6l2.2-2.2a1 1 0 0 1 1-.25 11.4 11.4 0 0 0 3.6.57 1 1 0 0 1 1 1V20a1 1 0 0 1-1 1A17 17 0 0 1 3 4a1 1 0 0 1 1-1h3.5a1 1 0 0 1 1 1c0 1.25.2 2.45.57 3.57a1 1 0 0 1-.25 1z" fill="#fff"/></svg>800-55512</div>
  <div class="abs topbar-sep" style="left:674px"></div>
  <div class="abs topbar-item" style="left:693px">
    <svg width="17" height="14" viewBox="0 0 24 18"><rect x="0" y="0" width="24" height="18" rx="2" fill="#fff"/><path d="M1 2l11 8 11-8" stroke="#ec1f27" stroke-width="2" fill="none"/></svg>info@corvane-mail.com</div>
  <div class="abs topbar-sep" style="left:913px"></div>
  <div class="abs topbar-item" style="left:934px">LOGIN</div>
  <div class="abs social-dot" style="left:1011px;top:12px;width:24px;height:24px"></div>
  <div class="abs social-dot" style="left:1050px;top:12px;width:24px;height:24px"></div>
  <div class="abs social-dot" style="left:1087px;top:12px;width:24px;height:24px"></div>

  <div class="abs brand"><span class="brand-square"></span>CORVANE</div>

  <nav class="nav">
    <a class="active" style="left:516px">Home</a>
    <a style="left:630px">About us</a>
    <a style="left:775px">Services</a>
    <a style="left:914px">Blog</a>
    <a style="left:1024px">Contact us</a>
  </nav>

  <!-- hero -->
  <div class="abs hero" role="img" aria-label="Cargo port at sunset with container cranes and a container ship"></div>
  <div class="abs hero-title">Corvane Imports</div>
  <div class="abs hero-sub">Retail &amp; whole sale import</div>
  <div class="abs hero-dot" style="top:378px"></div>
  <div class="abs hero-dot" style="top:398px;background:var(--red)"></div>
  <div class="abs hero-dot" style="top:418px"></div>
  <div class="abs hero-dot" style="top:438px"></div>
  <div class="abs hero-dot" style="top:458px"></div>

  <!-- about -->
  <h1 class="abs about-title">About <span>Corvane Imports</span></h1>
  <p class="abs about-lead">Neque porro quisquam est qui dolorem ipsum quia dolor sit amet, consectetur,</p>
  <p class="abs about-text">It is a long established fact that a reader will be distracted by the readable content of a page when looking at its layout. The point of using Lorem Ipsum is that it has a more-or-less normal distribution of letters, as opposed to using 'Content here, content here', making it look like readable English. Many desktop publishing packages and web page editors now use Lorem Ipsum as their default model text, and a search for 'lorem ipsum' will uncover many web sites still in their infancy.</p>

  <!-- services -->
  <div class="abs services"></div>
  <div class="abs services-dark"></div>
  <div class="abs worker" role="img" aria-label="Warehouse worker in a hard hat and safety vest holding a cardboard box"></div>
  <h2 class="abs services-title">Our Services</h2>
  <p class="abs services-text">t is a long established fact that a reader will be distracted by the readable content<br>&nbsp;of a page when looking at its layout. The point of using Lorem Ipsum</p>

  <div class="abs service-item" style="left:87px;top:1359px"><svg width="18" height="18" viewBox="0 0 20 20"><circle cx="10" cy="10" r="8.5" fill="none" stroke="#fff" stroke-width="1.6"/><path d="M6 10l3 3 6-7" fill="none" stroke="#fff" stroke-width="1.8"/></svg>Lorem ipsum dolor</div>
  <div class="abs service-item" style="left:87px;top:1408px"><svg width="18" height="18" viewBox="0 0 20 20"><circle cx="10" cy="10" r="8.5" fill="none" stroke="#fff" stroke-width="1.6"/><path d="M6 10l3 3 6-7" fill="none" stroke="#fff" stroke-width="1.8"/></svg>Aenean pellentesque</div>
  <div class="abs service-item" style="left:87px;top:1456px"><svg width="18" height="18" viewBox="0 0 20 20"><circle cx="10" cy="10" r="8.5" fill="none" stroke="#fff" stroke-width="1.6"/><path d="M6 10l3 3 6-7" fill="none" stroke="#fff" stroke-width="1.8"/></svg>Vestibulum bibendum</div>
  <div class="abs service-item" style="left:87px;top:1503px"><svg width="18" height="18" viewBox="0 0 20 20"><circle cx="10" cy="10" r="8.5" fill="none" stroke="#fff" stroke-width="1.6"/><path d="M6 10l3 3 6-7" fill="none" stroke="#fff" stroke-width="1.8"/></svg>Aenean vitae augue</div>
  <div class="abs service-item" style="left:369px;top:1359px"><svg width="18" height="18" viewBox="0 0 20 20"><circle cx="10" cy="10" r="8.5" fill="none" stroke="#fff" stroke-width="1.6"/><path d="M6 10l3 3 6-7" fill="none" stroke="#fff" stroke-width="1.8"/></svg>Ut tristique justo</div>
  <div class="abs service-item" style="left:369px;top:1408px"><svg width="18" height="18" viewBox="0 0 20 20"><circle cx="10" cy="10" r="8.5" fill="none" stroke="#fff" stroke-width="1.6"/><path d="M6 10l3 3 6-7" fill="none" stroke="#fff" stroke-width="1.8"/></svg>Duis porttitor nulla</div>
  <div class="abs service-item" style="left:369px;top:1456px"><svg width="18" height="18" viewBox="0 0 20 20"><circle cx="10" cy="10" r="8.5" fill="none" stroke="#fff" stroke-width="1.6"/><path d="M6 10l3 3 6-7" fill="none" stroke="#fff" stroke-width="1.8"/></svg>Proin rutrum leo</div>
  <div class="abs service-item" style="left:369px;top:1503px"><svg width="18" height="18" viewBox="0 0 20 20"><circle cx="10" cy="10" r="8.5" fill="none" stroke="#fff" stroke-width="1.6"/><path d="M6 10l3 3 6-7" fill="none" stroke="#fff" stroke-width="1.8"/></svg>Sed ultricies est tempor</div>

  <!-- blog -->
  <h2 class="abs blog-title">Latest Blog</h2>

  <article class="abs card" style="left:87px">
    <div class="card-img" style="position:relative;background:linear-gradient(135deg,#8a5a34,#3c2a20 60%,#6b4a30)" role="img" aria-label="Hands holding a tablet showing a world map in a warehouse aisle">
      <div class="card-date">02<small>JUN</small></div><div class="card-year">2018</div>
    </div>
    <h3 class="card-title">Neque porro quisquam</h3>
    <p class="card-body">It has survived not only five centuries, but also the leap into electronic typesetting,</p>
    <p class="card-more">Read More »</p>
  </article>

  <article class="abs card" style="left:441px">
    <div class="card-img" style="position:relative;background:linear-gradient(180deg,#6f9fd3,#c9c7c2 55%,#a55a3a)" role="img" aria-label="Freight trucks, containers, a cargo plane and a train at a logistics hub">
      <div class="card-date">02<small>JUN</small></div><div class="card-year">2018</div>
    </div>
    <h3 class="card-title">Dolorem ipsum quia</h3>
    <p class="card-body">It has survived not only five centuries, but also the leap into electronic typesetting, remaining</p>
    <p class="card-more">Read More »</p>
  </article>

  <article class="abs card" style="left:794px">
    <div class="card-img" style="position:relative;background:linear-gradient(135deg,#b08a62,#d8c2a2 50%,#3d5f9a)" role="img" aria-label="Worker scanning stacked cardboard boxes with a tablet">
      <div class="card-date">02<small>JUN</small></div><div class="card-year">2018</div>
    </div>
    <h3 class="card-title">Neque porro quisquam</h3>
    <p class="card-body">It has survived not only five centuries, but also the leap into electronic typesetting, remaining</p>
    <p class="card-more">Read More »</p>
  </article>

  <!-- cta -->
  <div class="abs cta"></div>
  <div class="abs cta-text">We are a retail &amp; whole sale import company</div>
  <div class="abs cta-phone"><svg width="22" height="22" viewBox="0 0 24 24"><path d="M6.6 10.8a15.5 15.5 0 0 0 6.6 6.6l2.2-2.2a1 1 0 0 1 1-.25 11.4 11.4 0 0 0 3.6.57 1 1 0 0 1 1 1V20a1 1 0 0 1-1 1A17 17 0 0 1 3 4a1 1 0 0 1 1-1h3.5a1 1 0 0 1 1 1c0 1.25.2 2.45.57 3.57a1 1 0 0 1-.25 1z" fill="#fff"/></svg>+66 (0) 2555 0148</div>

  <!-- footer -->
  <footer>
    <div class="abs footer"></div>
    <div class="abs footer-base"></div>
    <div class="abs footer-brand">CORVANE</div>

    <div class="abs footer-head" style="left:431px">CONTACT US</div>
    <div class="abs contact-label" style="left:431px;top:2596px"><svg width="20" height="15" viewBox="0 0 24 18"><rect x="1" y="1" width="22" height="16" rx="1" fill="none" stroke="#fff" stroke-width="1.6"/><path d="M1 2l11 8 11-8" stroke="#fff" stroke-width="1.6" fill="none"/></svg>EMAIL ADDRESS</div>
    <div class="abs contact-value" style="left:459px;top:2625px">hello@corvane-mail.com</div>
    <div class="abs contact-label" style="left:431px;top:2664px"><svg width="20" height="20" viewBox="0 0 24 24"><path d="M6.6 10.8a15.5 15.5 0 0 0 6.6 6.6l2.2-2.2a1 1 0 0 1 1-.25 11.4 11.4 0 0 0 3.6.57 1 1 0 0 1 1 1V20a1 1 0 0 1-1 1A17 17 0 0 1 3 4a1 1 0 0 1 1-1h3.5a1 1 0 0 1 1 1c0 1.25.2 2.45.57 3.57a1 1 0 0 1-.25 1z" fill="none" stroke="#fff" stroke-width="1.6"/></svg>PHONE NUMBER</div>
    <div class="abs contact-value" style="left:459px;top:2694px">+66 (0) 2555 0148</div>

    <div class="abs footer-head" style="left:752px">ABOUT</div>
    <div class="abs footer-link" style="left:754px;top:2597px">Home</div>
    <div class="abs footer-link" style="left:754px;top:2630px">About Us</div>
    <div class="abs footer-link" style="left:754px;top:2663px">Services</div>
    <div class="abs footer-link" style="left:754px;top:2696px">Contacts</div>

    <div class="abs footer-head" style="left:965px">SITE MAP</div>
    <div class="abs footer-link" style="left:967px;top:2597px">Product gallery</div>
    <div class="abs footer-link" style="left:967px;top:2630px">Privacy policy</div>
    <div class="abs footer-link" style="left:967px;top:2663px">Our Process</div>
    <div class="abs footer-link" style="left:967px;top:2696px">Useful Links</div>

    <div class="abs foot-social" style="left:500px"></div>
    <div class="abs foot-social" style="left:555px"></div>
    <div class="abs foot-social" style="left:611px"></div>
    <div class="abs foot-social" style="left:666px"></div>

    <div class="abs copyright">© 2018 Company Name &nbsp;All right reserved</div>
  </footer>

</div>
</body>
</html>
```